BOLD & MINIMALIST DESIGN NEEDED

We want a very bold but minimalistic business card design that is impactful and utilizes both sides of the business card. Our current logo is included for your use.

We want bold fonts and good use of negative space. We don't want the logo to overpower the design.

Target Market(s)

Professionals who are building new commercial buildings.

Industry/Entity Type

Construction

Contact Information for Business Card

Name, Title, email, office phone, cell phone, website

Font styles to use
Serif
Sans Serif

Requirements
Must have
• Bold design!

```html
<!DOCTYPE html>
<html lang="en">
<head>
<meta charset="utf-8">
<title>Summitline Design + Build — Business Card</title>
<link href="https://fonts.googleapis.com/css2?family=Montserrat:wght@400;500;800&display=swap" rel="stylesheet">
<style>
  :root {
    --ink: #111111;
    --green: #7dc242;
    --paper: #ffffff;
    --stage: #2a2a2a;
    --muted: #1c1c1c;
  }
  * { box-sizing: border-box; margin: 0; padding: 0; }
  html, body { width: 1200px; height: 874px; overflow: hidden; }
  body {
    background: var(--stage);
    font-family: "Montserrat", Arial, sans-serif;
    color: var(--ink);
    position: relative;
  }
  .card {
    position: absolute;
    left: 320px;
    width: 560px;
    height: 320px;
    background: var(--paper);
    border-radius: 18px;
    overflow: hidden;
  }
  .card--front { top: 60px; }
  .card--back { top: 494px; }

  .brand { display: flex; align-items: center; gap: 14px; }
  .brand__mark { width: 22px; height: 22px; background: var(--green); flex: none; }
  .brand__name {
    font-weight: 800;
    color: var(--ink);
    text-transform: uppercase;
    line-height: 1.05;
  }
  .card--front .brand {
    position: absolute; left: 0; right: 0; top: 0; bottom: 0;
    justify-content: center;
  }
  .card--front .brand__name { font-size: 44px; letter-spacing: 1px; }
  .card--front .brand__name small { display: block; font-size: 19px; letter-spacing: 6px; }

  .card--back .brand { position: absolute; left: 34px; top: 110px; gap: 10px; }
  .card--back .brand__mark { width: 16px; height: 16px; }
  .card--back .brand__name { font-size: 27px; }
  .card--back .brand__name small { display: block; font-size: 12px; letter-spacing: 4px; }

  .divider {
    position: absolute; left: 300px; top: 40px;
    width: 3px; height: 190px; background: var(--green);
  }
  .contact { position: absolute; left: 322px; top: 38px; }
  .contact__name { color: var(--green); font-weight: 800; font-size: 26px; letter-spacing: 1px; }
  .contact__title { font-size: 15px; font-weight: 500; letter-spacing: 1px; margin-top: 2px; }
  .contact__address { font-size: 15px; line-height: 1.4; margin-top: 14px; }
  .contact__list { list-style: none; margin-top: 12px; font-size: 15px; line-height: 1.55; }
  .contact__list li { display: flex; align-items: center; gap: 8px; }
  .contact__list svg { width: 13px; height: 13px; fill: var(--green); flex: none; }

  .band { position: absolute; left: 0; bottom: 0; width: 560px; height: 70px; }
</style>
</head>
<body>
  <section class="card card--front" aria-label="Card front">
    <div class="brand">
      <span class="brand__mark"></span>
      <span class="brand__name">Summitline<small>Design + Build</small></span>
    </div>
  </section>

  <section class="card card--back" aria-label="Card back">
    <div class="brand">
      <span class="brand__mark"></span>
      <span class="brand__name">Summitline<small>Design + Build</small></span>
    </div>

    <div class="divider"></div>

    <div class="contact">
      <p class="contact__name">RAVI MEHTA</p>
      <p class="contact__title">OWNER-CEO</p>
      <p class="contact__address">Your address, City<br>State, Zip 1234</p>
      <ul class="contact__list">
        <li><svg viewBox="0 0 16 16"><path d="M3 1h3l1 4-2 1c1 2 3 4 5 5l1-2 4 1v3c0 1-1 2-2 2C7 15 1 9 1 3c0-1 1-2 2-2z"/></svg>123 456 789</li>
        <li><svg viewBox="0 0 16 16"><path d="M4 0h8a1 1 0 0 1 1 1v14a1 1 0 0 1-1 1H4a1 1 0 0 1-1-1V1a1 1 0 0 1 1-1zm1 2v10h6V2z"/></svg>123 456 789</li>
        <li><svg viewBox="0 0 16 16"><path d="M0 3h16v10H0zm1 1 7 5 7-5z"/></svg>info@yourgmail.com</li>
        <li><svg viewBox="0 0 16 16"><circle cx="8" cy="8" r="7.5"/></svg>www.yourwebsite.com</li>
      </ul>
    </div>

    <svg class="band" viewBox="0 0 560 70" preserveAspectRatio="none" aria-hidden="true">
      <polygon points="0,0 360,28 380,70 0,70" fill="var(--muted)"/>
      <polygon points="360,28 560,44 560,70 380,70" fill="var(--green)"/>
    </svg>
  </section>
</body>
</html>
```